AI Business Tools Landing Page

My web-based website builder (Pavlora.com) will be adding many new features in the very near future and I need an eye-catching landing page to promote these new products.

The page will have a primary section of the 8 main products we are promoting:
1. AI Instant Website Generator
2. AI Chatbot
3. Online Store Builder with AI Assistance
4. AI Auto-Blogging System
5. Online Scheduling System
6. Custom Email System
7. SEO Service
8. CRM System

The page will also have a smaller section for links to our affiliate programs. These can be smaller, less-promanent buttons or links. These are the affiliate products:
1. Get Your LLC
2. Website Design and Maintenance
3. Search Ads Management
4. Social Media Posting Service
5. Logo Design
6. Trademark Registration
7. Patent Application
8. Printing Services (including postcards, flyers, and merch.)
9. Bulk AI Content Generator

The theme and color scheme of the page should follow the theme of our main website, which is https://pavlora.com.

I need the page fully coded and ready to deploy on my server.

I look forward to seeing your amazing designs!

```html
<!DOCTYPE html>
<html lang="en">
<head>
<meta charset="UTF-8">
<title>Pavlora – AI Business Tools</title>
<link rel="stylesheet" href="https://fonts.googleapis.com/css2?family=Poppins:wght@400;500;600;700&display=swap">
<style>
  :root{
    --navy:#0a1a33;
    --navy-deep:#061327;
    --navy-bar:#0d1f3c;
    --blue:#1e9ee6;
    --blue-light:#39b6f2;
    --ink:#14213a;
    --muted:#4a5568;
    --white:#ffffff;
    --line:#9fd6f5;
  }
  *{box-sizing:border-box;margin:0;padding:0}
  html,body{width:1200px;height:3084px;overflow:hidden}
  body{position:relative;background:var(--white);font-family:"Poppins",sans-serif;color:var(--ink)}

  /* Hero */
  .hero{position:absolute;left:0;top:0;width:1200px;height:520px;background:var(--navy);overflow:hidden}
  .hero-visual{position:absolute;right:0;top:0;width:640px;height:520px;
    background:radial-gradient(ellipse at 60% 45%,#5b6b82 0%,#2b3a52 40%,#0e1d36 75%,var(--navy) 100%)}
  .brand{position:absolute;display:flex;align-items:center;gap:12px;font-weight:600;color:var(--white)}
  .brand-mark{width:30px;height:30px;background:var(--blue);border-radius:6px}
  .hero .brand{left:112px;top:40px;font-size:26px}
  .hero-title{position:absolute;left:112px;top:230px;width:520px;font-size:40px;font-weight:500;line-height:1.25;color:var(--white)}
  .hero-title strong{font-weight:700}
  .hero-sub{position:absolute;left:112px;top:338px;font-size:15px;color:var(--white)}
  .btn{display:inline-block;font-weight:600;text-transform:uppercase;letter-spacing:.5px;text-decoration:none}
  .hero-cta{position:absolute;left:112px;top:384px;background:var(--blue);color:var(--white);font-size:13px;padding:11px 22px;border-radius:3px}
  .hero-wave{position:absolute;left:0;top:420px;width:1200px;height:110px}

  /* Sections */
  .section-title{position:absolute;left:0;width:1200px;text-align:center;font-size:34px;font-weight:600;color:var(--ink)}
  .tools-title{top:662px}
  .affiliates-title{top:2164px}

  /* Cards */
  .card{position:absolute;width:312px;height:552px;background:var(--white);
    box-shadow:0 6px 22px rgba(10,26,51,.16);display:flex;flex-direction:column}
  .card-media{height:220px;width:100%}
  .card-body{flex:1;padding:22px 24px 0}
  .card-title{font-size:23px;font-weight:600;line-height:1.25;text-align:center;color:var(--ink);margin-bottom:18px;min-height:58px;display:flex;align-items:center;justify-content:center}
  .card-title.is-active{color:var(--blue)}
  .card-list{list-style:none}
  .card-list li{position:relative;padding-left:28px;font-size:12.5px;line-height:1.55;color:var(--muted);margin-bottom:16px}
  .card-list li::before{content:"";position:absolute;left:0;top:3px;width:14px;height:14px;border-radius:50%;background:var(--navy)}
  .card-list li::after{content:"";position:absolute;left:4px;top:6px;width:5px;height:3px;border-left:2px solid var(--white);border-bottom:2px solid var(--white);transform:rotate(-45deg)}
  .card-list .example{color:var(--blue)}
  .card-link{height:46px;background:var(--navy-bar);color:var(--white);font-size:13px;display:flex;align-items:center;justify-content:center}
  .card-link.is-active{background:var(--blue-light)}
  .media-generator{background:linear-gradient(135deg,#0b2a4a,#1d6fa8 55%,#0a1a33)}
  .media-chatbot{background:linear-gradient(135deg,#0a2a55,#2b8fd6 50%,#0b1f40)}
  .media-store{background:linear-gradient(135deg,#c9cdd3,#7a8391 50%,#2e3540)}
  .media-blog{background:linear-gradient(135deg,#101a2e,#3a4a66 50%,#c79a58)}
  .media-schedule{background:linear-gradient(135deg,#5a4a3a,#b0a28f 45%,#2f3f58)}
  .media-email{background:linear-gradient(135deg,#e8e2d6,#a88b6a 50%,#3d3025)}

  .tools-more{position:absolute;left:420px;top:1984px;width:360px;height:50px;background:var(--navy-bar);color:var(--white);font-size:14px;display:flex;align-items:center;justify-content:center;gap:12px;border-radius:4px}

  /* Affiliates */
  .affiliate-art{position:absolute;left:450px;top:2250px;width:300px;height:300px;
    background:radial-gradient(circle at 50% 50%,#6fd0ff 0%,#1e9ee6 45%,rgba(30,158,230,0) 72%)}
  .affiliate-lines{position:absolute;left:0;top:2240px;width:1200px;height:400px}
  .affiliate{position:absolute;display:flex;align-items:center;gap:18px;font-size:17px;color:var(--ink);text-decoration:none}
  .affiliate.left{flex-direction:row-reverse;text-align:right;right:820px}
  .affiliate.right{left:800px}
  .affiliate-icon{width:44px;height:44px;border-radius:50%;background:var(--blue);flex:none;position:relative}
  .affiliate-icon::after{content:"";position:absolute;left:14px;top:14px;width:16px;height:16px;border:2px solid var(--white);border-radius:3px}

  /* Footer */
  .footer{position:absolute;left:0;top:2700px;width:1200px;height:384px;background:var(--navy-deep)}
  .footer-wave{position:absolute;left:0;top:2660px;width:1200px;height:100px}
  .footer .brand{left:116px;top:104px;font-size:28px}
  .footer-col{position:absolute;top:38px;color:var(--white)}
  .footer-col h3{font-size:26px;font-weight:600;color:var(--blue-light);letter-spacing:.5px;margin-bottom:14px}
  .footer-col p{font-size:14px;line-height:1.55;width:230px}
  .footer-col ul{list-style:none}
  .footer-col li{font-size:14px;line-height:1.7}
  .about{left:368px}
  .contact{left:680px}
  .follow{left:936px}
  .social{display:flex;flex-wrap:wrap;gap:10px;width:180px;margin-top:4px}
  .social span{width:22px;height:22px;border-radius:50%;background:var(--white)}
  .copyright{position:absolute;left:0;bottom:0;width:1200px;height:42px;border-top:1px solid #1d2d48;display:flex;align-items:center;justify-content:center;font-size:12px;color:var(--white)}
</style>
</head>
<body>

<header class="hero">
  <div class="hero-visual" role="img" aria-label="Humanoid robot with glowing circuitry looking forward"></div>
  <div class="brand"><span class="brand-mark"></span>Pavlora</div>
  <h1 class="hero-title">The Premier <strong>AI Website Builder</strong></h1>
  <p class="hero-sub">Generate your site now!</p>
  <a class="btn hero-cta" href="https://pavlora.com">Get Started</a>
  <svg class="hero-wave" viewBox="0 0 1200 110" preserveAspectRatio="none" aria-hidden="true">
    <path d="M0 60 C300 10 600 110 900 60 C1020 40 1120 30 1200 40 L1200 110 L0 110 Z" fill="#39b6f2"/>
    <path d="M0 78 C300 30 600 120 900 78 C1020 60 1120 52 1200 60 L1200 110 L0 110 Z" fill="#ffffff"/>
  </svg>
</header>

<h2 class="section-title tools-title">AI Business Tools</h2>

<article class="card" style="left:96px;top:780px">
  <div class="card-media media-generator" role="img" aria-label="Hand touching a holographic website interface"></div>
  <div class="card-body">
    <h3 class="card-title">AI Instant Website Generator</h3>
    <ul class="card-list">
      <li>Get a professional SEO optimized website in seconds!</li>
      <li>Includes custom domain, secure high speed hosting, professional images, and more!</li>
    </ul>
  </div>
  <a class="btn card-link" href="#">Learn More</a>
</article>

<article class="card" style="left:444px;top:780px">
  <div class="card-media media-chatbot" role="img" aria-label="Friendly chat robot with speech bubbles"></div>
  <div class="card-body">
    <h3 class="card-title">AI ChatBot</h3>
    <ul class="card-list">
      <li>Fully trainable ChatBot will learn about your business to automate the customer support process!</li>
      <li>Built in CRM features integrate emailing, text messaging.</li>
    </ul>
  </div>
  <a class="btn card-link" href="#">Learn More</a>
</article>

<article class="card" style="left:792px;top:780px">
  <div class="card-media media-store" role="img" aria-label="Laptop showing an online store with shopping bags"></div>
  <div class="card-body">
    <h3 class="card-title">Online Store Builder with AI Assistance</h3>
    <ul class="card-list">
      <li>Sell you products online and integrate your products into website!</li>
      <li>Accept payments from multiple payment gateways including CardFlow and PayNest!</li>
    </ul>
  </div>
  <a class="btn card-link" href="#">Learn More</a>
</article>

<article class="card" style="left:96px;top:1380px">
  <div class="card-media media-blog" role="img" aria-label="Robot writing blog posts at a desk"></div>
  <div class="card-body">
    <h3 class="card-title">AI Auto-Blogging System</h3>
    <ul class="card-list">
      <li>AI will generate an incredible blog for your business in seconds.</li>
      <li>Choose from daily, weekly, monthly automated blog posting. Consistent, unique, SEO optimized.</li>
    </ul>
  </div>
  <a class="btn card-link" href="#">Learn More</a>
</article>

<article class="card" style="left:444px;top:1380px">
  <div class="card-media media-schedule" role="img" aria-label="Robot assistant beside a calendar and clock"></div>
  <div class="card-body">
    <h3 class="card-title is-active">Online Scheduling System</h3>
    <ul class="card-list">
      <li>Get appointment bookings, restaurant reservations.</li>
      <li>Manage your employees' schedules and all your appointments from a simple, user-friendly dashboard!</li>
    </ul>
  </div>
  <a class="btn card-link is-active" href="#">Learn More</a>
</article>

<article class="card" style="left:792px;top:1380px">
  <div class="card-media media-email" role="img" aria-label="Envelopes and email icons on a desk"></div>
  <div class="card-body">
    <h3 class="card-title">Custom emails using your domain</h3>
    <ul class="card-list">
      <li>Quickly set up emails for yourself and all your employees with your own domain extension. <span class="example">example: john@yourdomain.com</span></li>
      <li>No more unprofessional MailBox and Yondermail email addresses!</li>
    </ul>
  </div>
  <a class="btn card-link" href="#">Learn More</a>
</article>

<a class="btn tools-more" href="#">View More AI Business Tools
  <svg width="18" height="12" viewBox="0 0 18 12" aria-hidden="true"><path d="M0 6 H15 M10 1 L16 6 L10 11" stroke="#fff" stroke-width="2" fill="none"/></svg>
</a>

<h2 class="section-title affiliates-title">Affiliate Programs</h2>

<svg class="affiliate-lines" viewBox="0 0 1200 400" aria-hidden="true">
  <g stroke="#9fd6f5" stroke-width="2" fill="none">
    <path d="M402 92 H470"/><path d="M402 184 H460"/><path d="M402 274 H460"/><path d="M402 362 H470"/>
    <path d="M730 90 H798"/><path d="M740 182 H798"/><path d="M740 272 H798"/><path d="M730 362 H798"/>
  </g>
</svg>
<div class="affiliate-art" role="img" aria-label="Abstract blue network graphic linking affiliate services"></div>

<a class="affiliate left" style="top:2310px" href="#"><span class="affiliate-icon"></span>Get Your LLC</a>
<a class="affiliate left" style="top:2388px" href="#"><span class="affiliate-icon"></span>Search Ads<br>Management</a>
<a class="affiliate left" style="top:2492px" href="#"><span class="affiliate-icon"></span>Logo Design</a>
<a class="affiliate left" style="top:2580px" href="#"><span class="affiliate-icon"></span>Patent Application</a>

<a class="affiliate right" style="top:2296px" href="#"><span class="affiliate-icon"></span>Website Design and<br>Maintenance</a>
<a class="affiliate right" style="top:2388px" href="#"><span class="affiliate-icon"></span>Social Media Posting<br>Service</a>
<a class="affiliate right" style="top:2490px" href="#"><span class="affiliate-icon"></span>Trademark Registration</a>
<a class="affiliate right" style="top:2580px" href="#"><span class="affiliate-icon"></span>Printing Services</a>

<svg class="footer-wave" viewBox="0 0 1200 100" preserveAspectRatio="none" aria-hidden="true">
  <path d="M0 30 C250 90 500 0 800 40 C1000 66 1120 40 1200 20 L1200 100 L0 100 Z" fill="#39b6f2"/>
  <path d="M0 52 C250 100 520 24 820 60 C1010 82 1120 60 1200 44 L1200 100 L0 100 Z" fill="#061327"/>
</svg>

<footer class="footer">
  <div class="brand"><span class="brand-mark"></span>Pavlora</div>
  <div class="footer-col about">
    <h3>ABOUT US</h3>
    <p>It'll take minutes or less! Just answer a few basic questions and watch your stunning new website generate in seconds!</p>
  </div>
  <div class="footer-col contact">
    <h3>CONTACT US</h3>
    <ul>
      <li>Terms &amp; Conditions</li>
      <li>FAQ</li>
      <li>Privacy Policy</li>
      <li>Contact Us</li>
    </ul>
  </div>
  <div class="footer-col follow">
    <h3>FOLLOW US</h3>
    <div class="social"><span></span><span></span><span></span><span></span><span></span><span></span><span></span><span></span><span></span><span></span></div>
  </div>
  <div class="copyright">© 2024 Pavlora. All Rights Reserved</div>
</footer>

</body>
</html>
```